Business card for a new cabinet shop company named Veloran Cabinets for high end cabinets

Design a business card, thinking dark rich green with colours to speak of high end luxury ie; cream, gold, black possibly

Mitchell Tarrowby
Director Craftsman
Email: info@veloranjoinery-example.com.au
Instagram : @veloran.cabinets

```html
<!DOCTYPE html>
<html lang="en">
<head>
<meta charset="utf-8">
<title>Veloran Cabinets – Business Card</title>
<link rel="stylesheet" href="https://fonts.googleapis.com/css2?family=Montserrat:wght@400;500;700&display=swap">
<style>
  :root {
    --backdrop: #161616;
    --card-green: #1f3d3b;
    --gold: #c9a863;
    --cream: #ffffff;
  }
  * { box-sizing: border-box; margin: 0; padding: 0; }
  html, body {
    width: 1200px;
    height: 1059px;
    overflow: hidden;
    background: var(--backdrop);
    font-family: "Montserrat", Arial, sans-serif;
  }
  .canvas { position: relative; width: 1200px; height: 1059px; }

  .card {
    position: absolute;
    left: 256px;
    width: 692px;
    height: 394px;
    border-radius: 28px;
    background: var(--card-green);
    overflow: hidden;
  }
  .card--front { top: 98px; }
  .card--back  { top: 553px; }

  .wordmark {
    position: absolute;
    left: 0;
    width: 100%;
    text-align: center;
    color: var(--gold);
    font-weight: 500;
    font-size: 44px;
    letter-spacing: 2px;
    line-height: 1;
  }
  .card--front .wordmark { top: 96px; }
  .card--back .wordmark  { top: 175px; font-size: 48px; }

  .holder {
    position: absolute;
    left: 40px;
    width: 248px;
    top: 236px;
    text-align: right;
  }
  .holder__name {
    color: var(--gold);
    font-weight: 700;
    font-size: 26px;
    line-height: 1;
    white-space: nowrap;
  }
  .holder__role {
    margin-top: 16px;
    color: var(--cream);
    font-weight: 400;
    font-size: 18px;
    line-height: 1;
    white-space: nowrap;
  }

  .divider {
    position: absolute;
    left: 315px;
    top: 238px;
    width: 1px;
    height: 64px;
    background: var(--gold);
  }

  .contacts {
    position: absolute;
    left: 339px;
    top: 243px;
    list-style: none;
  }
  .contacts__item {
    display: flex;
    align-items: center;
    gap: 9px;
    color: var(--cream);
    font-size: 15.5px;
    font-weight: 400;
    line-height: 1;
    white-space: nowrap;
  }
  .contacts__item + .contacts__item { margin-top: 18px; }
  .contacts__icon { width: 17px; height: 17px; flex: none; }
</style>
</head>
<body>
<main class="canvas">
  <section class="card card--front" aria-label="Business card front">
    <p class="wordmark">Veloran Cabinets</p>

    <div class="holder">
      <p class="holder__name">Mitchell Tarrowby</p>
      <p class="holder__role">Director Craftsman</p>
    </div>

    <span class="divider"></span>

    <ul class="contacts">
      <li class="contacts__item">
        <svg class="contacts__icon" viewBox="0 0 17 17" aria-hidden="true">
          <rect x="0.5" y="3" width="16" height="11" fill="var(--gold)"/>
          <path d="M0.5 3 L8.5 9.5 L16.5 3" fill="none" stroke="var(--card-green)" stroke-width="1.6"/>
        </svg>
        info@veloranjoinery-example.com.au
      </li>
      <li class="contacts__item">
        <svg class="contacts__icon" viewBox="0 0 17 17" aria-hidden="true">
          <rect x="1.5" y="1.5" width="14" height="14" rx="3" fill="none" stroke="var(--gold)" stroke-width="1.6"/>
        </svg>
        @veloran.cabinets
      </li>
    </ul>
  </section>

  <section class="card card--back" aria-label="Business card back">
    <p class="wordmark">Veloran Cabinets</p>
  </section>
</main>
</body>
</html>
```